Robotic Physical Therapy office needs a Grand Opening Flyer

We need a Grand Opening flyer design for a robotic physical therapy office named Kinetic Harbor Wellness. We would like it to have a clean, classy, upscale feeling that gives potential clients a V.I.P. feeling. We would like to use the colors black, gray, and yellow (logo will be uploaded).

Event: Thursday, June 1st, 2023 from 12pm-6pm
location: 58274 Pellham Ave, Bloomfield Hills, MI 48519

Industry/Entity Type

Physical therapy

Font styles to use
Script

Colors

Designer to choose colors to be used in the design.

Requirements
Nice to have
• More of a vip feel for the invite

```html
<!DOCTYPE html>
<html lang="en">
<head>
<meta charset="utf-8">
<title>Kinetic Harbor Wellness — Grand Opening</title>
<link href="https://fonts.googleapis.com/css2?family=Jost:wght@500;600&family=Lato:wght@700&display=swap" rel="stylesheet">
<style>
  :root {
    --ink: #18191b;
    --slate: #26343b;
    --teal: #34505a;
    --white: #ffffff;
    --yellow: #f7dc2c;
  }
  * { margin: 0; padding: 0; box-sizing: border-box; }
  html, body { width: 912px; height: 1200px; overflow: hidden; background: var(--ink); }
  .flyer {
    position: relative;
    width: 912px;
    height: 1200px;
    overflow: hidden;
    background: var(--ink);
    font-family: "Jost", sans-serif;
    color: var(--white);
  }
  .hero-photo {
    position: absolute;
    left: 0;
    top: 0;
    width: 912px;
    height: 900px;
    background:
      radial-gradient(ellipse 45% 35% at 30% 30%, rgba(80, 110, 120, 0.5), transparent 70%),
      radial-gradient(ellipse 35% 30% at 82% 55%, rgba(70, 100, 115, 0.45), transparent 70%),
      linear-gradient(180deg, var(--slate) 0%, var(--teal) 40%, #24313a 75%, var(--ink) 100%);
  }
  .frame { position: absolute; inset: 0; width: 912px; height: 1200px; }
  .brand {
    position: absolute;
    top: 158px;
    left: 0;
    width: 100%;
    text-align: center;
    font-family: "Lato", sans-serif;
    font-weight: 700;
    color: var(--yellow);
    font-size: 33px;
    line-height: 1.08;
    letter-spacing: 0.5px;
  }
  .headline {
    position: absolute;
    left: 0;
    width: 100%;
    text-align: center;
    font-weight: 600;
    line-height: 1;
    letter-spacing: -1px;
  }
  .headline--grand { top: 392px; font-size: 150px; color: var(--white); }
  .headline--opening { top: 523px; font-size: 150px; color: var(--yellow); }
  .event-date {
    position: absolute;
    top: 708px;
    width: 100%;
    text-align: center;
    font-weight: 500;
    font-size: 50px;
    line-height: 1;
    letter-spacing: -0.5px;
  }
  .event-time {
    position: absolute;
    top: 771px;
    width: 100%;
    text-align: center;
    font-weight: 500;
    font-size: 41px;
    line-height: 1;
  }
  .address {
    position: absolute;
    top: 1014px;
    width: 100%;
    text-align: center;
    font-weight: 500;
    font-size: 35px;
    line-height: 1.05;
  }
</style>
</head>
<body>
<main class="flyer">
  <div class="hero-photo" role="img" aria-label="Dark, softly blurred photo of a robotic therapy arm and a glowing circuit brain in slate and teal tones"></div>

  <svg class="frame" viewBox="0 0 912 1200" aria-hidden="true">
    <g fill="none" stroke="var(--white)" stroke-width="4">
      <rect x="8" y="8" width="896" height="1184"/>
      <rect x="27" y="27" width="858" height="1146"/>
    </g>
  </svg>

  <p class="brand">KINETIC HARBOR<br>WELLNESS</p>

  <h1>
    <span class="headline headline--grand">GRAND</span>
    <span class="headline headline--opening">OPENING</span>
  </h1>

  <p class="event-date">THURSDAY, JUNE 1ST, 2023</p>
  <p class="event-time">FROM 12PM-6PM</p>

  <p class="address">58274 PELLHAM AVE, BLOOMFIELD<br>HILLS, MI 48519</p>
</main>
</body>
</html>
```